Brightwell Supports

We need an updated website that captures the comprehensive services and supports we provide to persons with developmental disabilities. We need a website design that educates families about the services we provide. We would also need a website that is user-friendly so that we could periodically update training schedules and ongoing programming.

• Thank you for submitting designs.  A few things I am hoping to see offered in the website:
• Front page highlights the services we offer (host homes, family caregiver, day program, employment program, SLS program, supported apartment program, behavior/clinical program)
• Front page also highlights any new programs we want to make prominent:  family caregiver, future restaurant employment openings, etc...
• Interactive Training Calendar
• Employee Resources page (link to carevo, email login, etc.)
• Uniform provider application for host home providers
• Information on agency - history, goals, etc.
• Contact Information/Location

 

Fun things to include:

• Client Highlights (featuring a client story each month, etc...)
• Employee highlights (featuring a staff member...)
• link to other Brightwell business pages (Brightwell Therapy and Brightwell Restaurant)

```html
<!DOCTYPE html>
<html lang="en">
<head>
<meta charset="utf-8">
<title>Brightwell Supports</title>
<link href="https://fonts.googleapis.com/css2?family=Arimo:wght@400;700&family=Gelasio:ital,wght@0,400;1,400&display=swap" rel="stylesheet">
<style>
:root{
  --brand:#8a0c12;
  --brand-dark:#6a0008;
  --ink:#555;
  --ink-dark:#333;
  --muted:#a3a3a3;
  --line:#d9d9d9;
  --btn-top:#6d737b;
  --btn-bottom:#4b5058;
  --hero-top:#9fb9c7;
  --hero-bottom:#2a4957;
  --white:#fff;
}
*{margin:0;padding:0;box-sizing:border-box}
html,body{width:1058px;height:1200px;overflow:hidden;background:var(--white)}
body{position:relative;font-family:"Arimo",Arial,sans-serif;color:var(--ink)}
.abs{position:absolute}
.serif{font-family:"Gelasio",Georgia,serif}

/* header */
.brand-name{left:156px;top:28px;font-family:"Gelasio",Georgia,serif;font-size:24px;color:var(--brand);letter-spacing:.5px}
.brand-dot{left:140px;top:36px;width:11px;height:11px;border-radius:50%;background:var(--brand)}
.tagline{left:158px;top:60px;font-family:"Gelasio",Georgia,serif;font-style:italic;font-size:9px;color:var(--brand)}
.main-nav a{position:absolute;top:33px;font-size:11.5px;color:#555;text-decoration:none}

/* hero */
.hero{left:0;top:80px;width:1058px;height:299px;background:linear-gradient(170deg,var(--hero-top) 0%,#5f7f90 45%,var(--hero-bottom) 100%)}
.hero-arrow{top:205px;width:40px;height:40px}
.hero-caption{left:152px;top:261px;width:414px;height:75px;background:rgba(20,22,24,.82);border-left:5px solid var(--brand);color:var(--white);padding:18px 0 0 14px}
.hero-caption h2{font-weight:400;font-size:14px;letter-spacing:.3px}
.hero-caption p{font-size:12.5px;margin-top:8px}

/* welcome */
.welcome{left:0;top:404px;width:1058px;text-align:center}
.welcome h1{font-family:"Gelasio",Georgia,serif;font-weight:400;font-size:30px;color:var(--muted)}
.welcome p{font-size:11.2px;line-height:19px;margin:15px auto 0;width:640px;color:#666}
.rule{left:152px;top:510px;width:755px;height:1px;background:var(--line)}

/* about */
.photo{background:linear-gradient(160deg,#eef0f1,#c9ced2 60%,#8f9aa3)}
.about-photo{left:152px;top:541px;width:250px;height:172px}
.about h3{position:absolute;left:427px;top:538px;font-family:"Gelasio",Georgia,serif;font-weight:400;font-size:17px;color:var(--brand)}
.about-text{left:428px;top:569px;width:250px;font-size:9.4px;line-height:19px;color:#666}
.contact-line{left:428px;font-size:9.8px;color:var(--ink-dark);display:flex;align-items:center;gap:6px}
.btn{position:absolute;display:flex;align-items:center;justify-content:center;color:var(--white);background:linear-gradient(var(--btn-top),var(--btn-bottom));border:1px solid #3d4147;border-radius:3px;text-decoration:none}
.btn-contact{left:546px;top:730px;width:131px;height:32px;font-size:12px}

/* services menu */
.services-menu{left:707px;top:538px;width:200px;list-style:none}
.services-menu li{height:22px;margin-bottom:4.4px;border:1px solid var(--line);font-size:8.2px;color:#555;display:flex;align-items:center;justify-content:space-between;padding:0 9px 0 12px}
.services-menu li.active{background:var(--brand);border-color:var(--brand);color:var(--white)}
.services-menu li span.chev{font-size:8px;color:#999}
.services-menu li.active span.chev{color:var(--white)}

/* feature columns */
.feature h3{position:absolute;top:806px;font-family:"Gelasio",Georgia,serif;font-weight:400;font-size:16px;color:var(--brand)}
.feature .photo{position:absolute;top:840px;width:232px;height:122px}
.feature p{position:absolute;top:974px;width:236px;font-size:9.4px;line-height:16.6px;color:#666}
.feature .btn{top:1052px;width:78px;height:24px;font-size:9.5px}
.photo-employment{background:linear-gradient(#f4f4f4,#cfc6bd 60%,#9e9285)}
.photo-clients{background:linear-gradient(135deg,#f2f2f2,#d9b9a2 50%,#2f333a)}
.photo-sls{background:linear-gradient(#34598a,#7e9fc3 55%,#3e6c60)}

/* footer */
.site-footer{left:0;top:1116px;width:1058px;height:84px;background:var(--brand-dark);color:var(--white)}
.footer-nav{left:153px;top:23px;font-size:9.6px;display:flex;gap:18px}
.footer-nav a{color:var(--white);text-decoration:none}
.copyright{left:153px;top:48px;font-size:9.6px}
.connect{left:640px;top:31px;font-family:"Gelasio",Georgia,serif;font-style:italic;font-size:8.5px;line-height:13px;text-align:right}
.social{left:744px;top:36px;display:flex;gap:19px}
.social span{width:11px;height:11px;border-radius:50%;background:var(--white);opacity:.9}
</style>
</head>
<body>

<header>
  <span class="abs brand-dot"></span>
  <div class="abs brand-name">Brightwell Supports</div>
  <div class="abs tagline">Building Abilities ~ Creating Opportunities ~ Developing Relationships</div>
  <nav class="main-nav">
    <a href="#" style="left:549px">Home</a>
    <a href="#" style="left:636px">About us</a>
    <a href="#" style="left:742px">Contact Us</a>
    <a href="#" style="left:856px">Location</a>
  </nav>
</header>

<section class="abs hero" role="img" aria-label="Photo of a tall cable-stayed bridge crossing a misty valley">
</section>
<svg class="abs hero-arrow" style="left:73px" viewBox="0 0 40 40" aria-hidden="true"><circle cx="20" cy="20" r="18" fill="none" stroke="rgba(255,255,255,.35)" stroke-width="2"/><path d="M24 11 13 20l11 9z" fill="rgba(255,255,255,.35)"/></svg>
<svg class="abs hero-arrow" style="left:942px" viewBox="0 0 40 40" aria-hidden="true"><circle cx="20" cy="20" r="18" fill="none" stroke="rgba(0,0,0,.35)" stroke-width="2"/><path d="M16 11l11 9-11 9z" fill="rgba(0,0,0,.35)"/></svg>
<div class="abs hero-caption">
  <h2>BRIGHTWELL SUPPORTS</h2>
  <p>Building Abilities ~ Creating Opportunities ~ Developing Relationships</p>
</div>

<section class="abs welcome">
  <h1>Welcome to Brightwell Supports</h1>
  <p>Brightwell Supports is an agency designed to creatively serve individuals with developmental disabilities in community-based settings throughout Colorado.&nbsp; Brightwell Supports is an approved service agency through the Division of Developmental Disabilities.</p>
</section>
<div class="abs rule"></div>

<section class="about">
  <div class="abs photo about-photo" role="img" aria-label="Photo of a team of four colleagues around a meeting table with a laptop"></div>
  <h3>About Brightwell Supports</h3>
  <p class="abs about-text">Connected independence" for individuals to continually develop necessary skills to live as an integrated member of their communities. Through supported employment services and resourceful providers, clients are able to access their communities in a new and meaningful way.</p>
  <div class="abs contact-line" style="top:674px">
    <svg width="9" height="11" viewBox="0 0 9 11"><path d="M4.5 0A4.2 4.2 0 0 0 .3 4.2C.3 7.3 4.5 11 4.5 11s4.2-3.7 4.2-6.8A4.2 4.2 0 0 0 4.5 0z" fill="#333"/><circle cx="4.5" cy="4.2" r="1.5" fill="#fff"/></svg>
    415 Alder Ridge Road ~ Pinecrest, CO 80312
  </div>
  <div class="abs contact-line" style="top:697px">
    <svg width="8" height="12" viewBox="0 0 8 12"><rect x=".7" y=".7" width="6.6" height="10.6" rx="1.2" fill="none" stroke="#333" stroke-width="1.2"/><rect x="3" y="9" width="2" height="1" fill="#333"/></svg>
    Phone: 720-555-0148,
    <svg style="margin-left:14px" width="11" height="10" viewBox="0 0 11 10"><rect x="2.5" y="0" width="6" height="3" fill="#333"/><rect x="0" y="3" width="11" height="4.5" rx="1" fill="#333"/><rect x="2.5" y="6" width="6" height="4" fill="#333"/><rect x="3.5" y="7" width="4" height="2" fill="#fff"/></svg>
    Fax: 303-555-0192
  </div>
  <a href="#" class="btn btn-contact">Contact Now</a>
</section>

<ul class="abs services-menu">
  <li class="active">Available Services<span class="chev">&raquo;</span></li>
  <li>Residential Program<span class="chev">&raquo;</span></li>
  <li>Day/Employment Program<span class="chev">&raquo;</span></li>
  <li>SLS Program<span class="chev">&raquo;</span></li>
  <li>Become a Provider<span class="chev">&raquo;</span></li>
  <li>Meet Our Team!<span class="chev">&raquo;</span></li>
  <li>Activity Calendar<span class="chev">&raquo;</span></li>
  <li>Training Calendar<span class="chev">&raquo;</span></li>
  <li>Community Resources<span class="chev">&raquo;</span></li>
</ul>

<section class="feature">
  <h3 style="left:153px">Employment</h3>
  <div class="photo photo-employment" style="left:152px" role="img" aria-label="Photo of a cheering group of people raising their arms"></div>
  <p style="left:154px">Promoting "connected independence" for individuals to continually develop necessary skills to live as an inte-grated member of their communities. Through supported employment services and resourceful providers...</p>
  <a href="#" class="btn" style="left:153px">Read More</a>
</section>
<section class="feature">
  <h3 style="left:412px">Client Supports</h3>
  <div class="photo photo-clients" style="left:412px" role="img" aria-label="Photo of several hands stacked together in teamwork"></div>
  <p style="left:414px">Promoting "connected independence" for individuals to continually develop necessary skills to live as an inte-grated member of their communities. Through supported employment services and resourceful providers...</p>
  <a href="#" class="btn" style="left:413px">Read More</a>
</section>
<section class="feature">
  <h3 style="left:675px">SLS Services</h3>
  <div class="photo photo-sls" style="left:675px" role="img" aria-label="Photo of green signposts pointing to opportunity against a blue sky"></div>
  <p style="left:677px">Promoting "connected independence" for individuals to continually develop necessary skills to live as an inte-grated member of their communities. Through supported employment services and resourceful providers...</p>
  <a href="#" class="btn" style="left:676px">Read More</a>
</section>

<footer class="abs site-footer">
  <nav class="abs footer-nav">
    <a href="#">Home</a><span>|</span><a href="#">About us</a><span>|</span><a href="#">Contact Us</a><span>|</span><a href="#">Location</a>
  </nav>
  <div class="abs copyright">Copyrights. &copy; 2014. Brightwell Supports. All rights reserved.</div>
  <div class="abs connect">Connect with<br>our social network :</div>
  <div class="abs social" aria-label="Social network links">
    <span></span><span></span><span></span><span></span><span></span><span></span>
  </div>
</footer>

</body>
</html>
```